Kampfsport Außenwerbung
Zielgruppe
Kampfsportschule für Kinder, Jugendliche und Erwachsene. Sportarten: Kick-Boxen, Jiu-Jitsu und Tricking
Aufgabenstellung
Ich bräuchte für meine Schaufenster eine schöne Außenwerbung. Beworben werden sollen alle meine Sportarten. Ich lade meinen Flyer hoch, damit im ähnlichen Stil gearbeitet werden kann. Außerdem auch noch andere Beispiele an denen man sich orientieren kann, sowie mein Logo und meine Fensterfront.

```html
<!DOCTYPE html>
<html lang="de">
<head>
<meta charset="utf-8">
<title>Martial Arts Borq – Rollup</title>
<link rel="stylesheet" href="https://fonts.googleapis.com/css2?family=Russo+One&family=Krona+One&family=Exo+2:wght@500;600;700&display=swap">
<style>
  :root {
    --page: #eeeff1;
    --black: #0d0d0f;
    --red: #e01f26;
    --red-dark: #8c181c;
    --white: #ffffff;
    --grey-light: #f1f1f0;
    --grey-mid: #c2bebb;
    --ink: #161616;
  }
  html, body { margin: 0; padding: 0; overflow: hidden; }
  body { width: 1200px; height: 1200px; background: var(--page); }
  .canvas { display: block; width: 1200px; height: 1200px; }
  .headline { font-family: "Russo One", sans-serif; font-style: italic; fill: var(--grey-light); }
  .tagline { font-family: "Exo 2", sans-serif; font-weight: 700; font-style: italic; fill: var(--white); letter-spacing: 4px; }
  .section-title { font-family: "Krona One", sans-serif; fill: var(--red); }
  .discipline { font-family: "Krona One", sans-serif; fill: var(--ink); }
  .claim { font-family: "Exo 2", sans-serif; font-weight: 700; fill: var(--white); letter-spacing: 2.5px; }
  .lead { font-family: "Krona One", sans-serif; fill: var(--white); }
  .address { font-family: "Exo 2", sans-serif; font-weight: 500; fill: var(--white); letter-spacing: 1px; }
  .info-title { font-family: "Krona One", sans-serif; fill: var(--red); }
  .contact { font-family: "Exo 2", sans-serif; font-weight: 600; fill: var(--white); letter-spacing: 1.5px; }
  .brand-name { font-family: "Russo One", sans-serif; fill: var(--white); }
</style>
</head>
<body>
<svg class="canvas" viewBox="0 0 1500 1500" xmlns="http://www.w3.org/2000/svg">
  <defs>
    <linearGradient id="grey-panel" x1="0" y1="0" x2="0" y2="1">
      <stop offset="0" stop-color="#f3f3f2"/>
      <stop offset="1" stop-color="#b9b4b0"/>
    </linearGradient>
    <linearGradient id="corner-fade" x1="0" y1="0" x2="0" y2="1">
      <stop offset="0" stop-color="#ffffff"/>
      <stop offset="0.4" stop-color="#ffffff"/>
      <stop offset="1" stop-color="#6d6d72"/>
    </linearGradient>
    <linearGradient id="photo-fill" x1="0" y1="0" x2="0" y2="1">
      <stop offset="0" stop-color="#2a2224"/>
      <stop offset="0.5" stop-color="#3b3334"/>
      <stop offset="1" stop-color="#1a1a1c"/>
    </linearGradient>
  </defs>

  <g class="banner" transform="translate(457 83)">
    <!-- base -->
    <rect class="banner-base" width="586" height="1334" fill="var(--black)"/>

    <!-- top X bands -->
    <g class="top-bands">
      <polygon points="0,0 240,0 300,120 0,360" fill="var(--red-dark)"/>
      <polygon points="65,0 205,0 0,300 0,130" fill="var(--red)"/>
      <polygon points="0,0 20,0 80,140 0,245" fill="url(#corner-fade)"/>
      <polygon points="586,0 346,0 286,120 586,360" fill="var(--red-dark)"/>
      <polygon points="521,0 381,0 586,300 586,130" fill="var(--red)"/>
      <polygon points="586,0 566,0 506,140 586,245" fill="url(#corner-fade)"/>
    </g>

    <!-- brand mark -->
    <g class="brand" transform="translate(293 190)">
      <circle cx="-110" cy="-4" r="14" fill="var(--red)"/>
      <text class="brand-name" x="14" y="6" font-size="26" text-anchor="middle">Martial Arts Borq</text>
    </g>

    <!-- middle grey panel and diagonal bands -->
    <polygon class="grey-panel" points="0,493 586,493 586,910 0,700" fill="url(#grey-panel)"/>
    <polygon points="0,700 586,905 586,945 0,730" fill="var(--red)"/>
    <polygon points="0,730 586,945 586,1020 0,810" fill="var(--red-dark)"/>

    <!-- bottom accents -->
    <polygon points="586,1025 514,1082 586,1140" fill="var(--red)"/>
    <polygon points="270,1334 586,1215 586,1275 430,1334" fill="var(--red-dark)"/>
    <polygon points="430,1334 586,1275 586,1334" fill="var(--red)"/>

    <!-- photo area -->
    <rect class="hero-photo" x="368" y="215" width="218" height="730" rx="8" fill="url(#photo-fill)"
          role="img" aria-label="Foto: Mädchen im Kampfsportanzug mit gelbem Gürtel beim Standspagat"/>

    <!-- headline -->
    <text class="headline" x="37" y="345" font-size="48">MARTIAL</text>
    <text class="headline" x="25" y="390" font-size="48">ARTS BORQ</text>
    <text class="tagline" x="20" y="445" font-size="19">KAMPFSPORT</text>
    <text class="tagline" x="20" y="469" font-size="19">&amp; SELBSTVERTEIDIGUNG</text>

    <!-- disciplines -->
    <text class="section-title" x="18" y="562" font-size="31">DISZIPLINEN:</text>
    <text class="discipline" x="18" y="601" font-size="16">.Kick-Boxen/Sportkarate</text>
    <text class="discipline" x="18" y="627" font-size="16">.Jiu-Jitsu Selbstverteidigung</text>
    <text class="discipline" x="18" y="654" font-size="16">.Tricking</text>
    <text class="discipline" x="18" y="680" font-size="16">.U25 Kick-Boxen</text>

    <!-- claim -->
    <text class="claim" x="57" y="966" font-size="36">WIR MACHEN</text>
    <text class="claim" x="57" y="1008" font-size="36">KINDER STARK!</text>

    <!-- lead & address -->
    <text class="lead" x="56" y="1073" font-size="19">Leitung: Timo Borq</text>
    <text class="address" x="56" y="1101" font-size="20">Am Werkhof 4c | 26599 Nordheide</text>

    <!-- info -->
    <line x1="0" y1="1156" x2="48" y2="1156" stroke="var(--red)" stroke-width="3"/>
    <text class="info-title" x="56" y="1163" font-size="19">INFO &amp; PROBETRAINING:</text>
    <line x1="474" y1="1156" x2="586" y2="1156" stroke="var(--red)" stroke-width="3"/>

    <g class="icon-phone" transform="translate(75 1200)" fill="none" stroke="var(--red)" stroke-width="2.5">
      <circle r="15"/>
      <path d="M-6,-6 q-2,8 5,13 q4,3 7,1 l1,-3 -4,-3 -2,2 q-4,-2 -5,-6 l2,-2 -2,-4 z" fill="var(--red)" stroke="none"/>
    </g>
    <text class="contact" x="114" y="1211" font-size="27">0151/ 2038 7741</text>

    <g class="icon-mail" transform="translate(58 1234)" fill="none" stroke="var(--red)" stroke-width="2.2">
      <rect width="34" height="22"/>
      <polyline points="0,0 17,13 34,0"/>
      <polyline points="0,22 13,10"/>
      <polyline points="34,22 21,10"/>
    </g>
    <text class="contact" x="114" y="1253" font-size="25">info@martial-arts-borq.de</text>
  </g>
</svg>
</body>
</html>
```